real esate business card with company logo and name

we need a business card design for a real esate company

The company name is Walsh & Brand Pty Ltd, and we have our logo designed and will upload. We want classic or moden feel. Black or white background. looks more textured. Should include folowinginformations
Owen Walsh and Lucy Brand
Sales Agents & Onsite Manager
p: 07 5948 2063
F: 07 5948 2174
M:0431 857 219
3/42 Marlow Crescent, FERNLEA QLD 4213

We want this business card looks professonal. Thank you in advance.

Industry/Entity Type

Real Estate Agent

Contact Information for Business Card

Owen Walsh and Lucy Brand
Onsite Manager & Sales Agents
p: 07 5948 2063
M:0431 857 219

Font styles to use
Serif

Colors
000000
fbfbfb
333333
959595

Requirements
Must have
• company logo and name, black or white back ground

```html
<!DOCTYPE html>
<html lang="en">
<head>
<meta charset="utf-8">
<title>Walsh &amp; Brand Pty Ltd – Business Card</title>
<link rel="stylesheet" href="https://fonts.googleapis.com/css2?family=Open+Sans:wght@400;600&display=swap">
<style>
  :root {
    --ink: #000000;
    --ink-soft: #333333;
    --brand-grey: #6f6f6f;
    --mark-grey: #959595;
    --card: #fbfbfb;
    --backdrop: #e6e6e6;
    --edge: #d4d4d4;
  }
  * { margin: 0; padding: 0; box-sizing: border-box; }
  html, body {
    width: 1200px;
    height: 952px;
    overflow: hidden;
    background: var(--backdrop);
    font-family: "Open Sans", sans-serif;
  }
  .card {
    position: absolute;
    left: 100px;
    top: 166px;
    width: 1000px;
    height: 620px;
    background: linear-gradient(160deg, #ffffff 0%, var(--card) 55%, #f3f3f3 100%);
    border: 1px solid var(--edge);
    border-radius: 6px;
    box-shadow: 0 14px 40px rgba(0,0,0,0.12);
  }
  .holder-names {
    position: absolute;
    left: 70px;
    top: 78px;
    font-size: 40px;
    font-weight: 400;
    color: var(--ink);
    letter-spacing: 0.2px;
  }
  .holder-role {
    position: absolute;
    left: 86px;
    top: 134px;
    font-size: 24px;
    color: var(--ink-soft);
  }
  .contact-list {
    position: absolute;
    left: 150px;
    top: 240px;
    width: 340px;
    list-style: none;
    text-align: center;
  }
  .contact-item { margin-bottom: 26px; }
  .contact-icon {
    display: block;
    width: 22px;
    height: 22px;
    margin: 0 auto 8px;
  }
  .contact-text {
    font-size: 24px;
    color: var(--ink);
    line-height: 1.3;
  }
  .brand-block {
    position: absolute;
    left: 570px;
    top: 120px;
    width: 400px;
    text-align: center;
  }
  .brand-square {
    display: block;
    width: 230px;
    height: 230px;
    margin: 0 auto 44px;
    background: var(--mark-grey);
  }
  .brand-name {
    font-size: 28px;
    font-weight: 600;
    letter-spacing: 1.5px;
    color: var(--brand-grey);
    white-space: nowrap;
  }
</style>
</head>
<body>
  <main class="card">
    <h1 class="holder-names">Owen Walsh and Lucy Brand</h1>
    <p class="holder-role">Onsite Manager &amp; Sales Agents</p>

    <ul class="contact-list">
      <li class="contact-item">
        <svg class="contact-icon" viewBox="0 0 22 22" aria-hidden="true">
          <rect width="22" height="22" fill="#000"/>
          <path d="M6 4.5l3 0.5 1 3.5-2 1.2c0.9 2 2.3 3.4 4.3 4.3l1.2-2 3.5 1 0.5 3c-1 1.2-2.5 1.6-4 1-4.2-1.5-7.2-4.5-8.7-8.7-0.5-1.5-0.1-3 1.2-3.8z" fill="#fff"/>
        </svg>
        <span class="contact-text">07 5948 2063</span>
      </li>
      <li class="contact-item">
        <svg class="contact-icon" viewBox="0 0 22 22" aria-hidden="true">
          <rect width="22" height="22" fill="#000"/>
          <rect x="7" y="3.5" width="8" height="15" rx="1.2" fill="#fff"/>
          <rect x="8.5" y="5.5" width="5" height="8" fill="#000"/>
          <circle cx="11" cy="16" r="1" fill="#000"/>
        </svg>
        <span class="contact-text">0431 857 219</span>
      </li>
      <li class="contact-item">
        <svg class="contact-icon" viewBox="0 0 22 22" aria-hidden="true">
          <rect width="22" height="22" fill="#000"/>
          <path d="M11 4l7 6.5h-2v7h-3.5v-4.5h-3v4.5H6v-7H4z" fill="#fff"/>
        </svg>
        <span class="contact-text">3/42 Marlow Crescent,<br>FERNLEA QLD 4213</span>
      </li>
    </ul>

    <div class="brand-block">
      <span class="brand-square" role="img" aria-label="Walsh &amp; Brand company mark"></span>
      <p class="brand-name">WALSH &amp; BRAND PTY LTD.</p>
    </div>
  </main>
</body>
</html>
```